Bright bears day nursery qrp limited

we would like create a website that can be updated by us easily as we have regular changes to what we provide and need. we would like something that is classy but also appealing from a child's aspect. we would be looking to add our own logo and our kinderwatch logo both attached, if you guys can create it and we will work with the preferred choice to add all the text.
We would like the links to family pathways, kinderwatch report and our chatterbook feed on the front page

we are looking for a website for our childcare business we have 2 nurseries that we would like one website.
showing our opening hours, price list, policies etc as well as photos, description of our day, staff photos and their training accreditation's.

Target Market(s)

Families

Industry/Entity Type

Childcare

Number of Pages Required

5+ page

Font styles to use
Serif

Colors

Designer to choose colors to be used in the design.

Requirements
Must have
• links to social media and other websites, photographs, links to download registration forms etc, parents able to leave reviews. google maps link, job opportunities
Nice to have
• facilities to take payments

```html
<!DOCTYPE html>
<html lang="en">
<head>
<meta charset="utf-8">
<title>Bright Bears Day Nursery QRP</title>
<link rel="stylesheet" href="https://fonts.googleapis.com/css2?family=Open+Sans:wght@400;600;700;800&display=swap">
<style>
:root{
  --navy:#0c3a7e;
  --navy-dark:#082c63;
  --green:#4dae48;
  --green-bright:#5cc04a;
  --magenta:#c2197e;
  --ink:#333;
  --muted:#777;
  --light:#f0f0f0;
  --footer:#3a3a3a;
  --white:#fff;
  --row:#e8e8ea;
}
*{box-sizing:border-box;margin:0;padding:0}
html,body{width:1200px;height:3659px;overflow:hidden}
body{font-family:"Open Sans",Arial,sans-serif;color:var(--ink);background:var(--white);position:relative}
.abs{position:absolute}
.header{height:185px;position:relative}
.brand{position:absolute;top:40px;width:200px;text-align:center;color:var(--navy);font-weight:800;font-size:26px;line-height:1.15}
.brand .dot{display:block;width:26px;height:26px;margin:0 auto 8px;background:var(--magenta)}
.nav{position:absolute;top:185px;left:0;width:1200px;height:36px;background:var(--navy);display:flex;justify-content:center}
.nav a{color:var(--white);text-decoration:none;font-size:13px;font-weight:600;line-height:36px;width:160px;text-align:center}
.nav a.active{background:var(--navy-dark)}
.hero{position:absolute;top:221px;left:0;width:1200px;height:394px;background:linear-gradient(120deg,#6fb7b0 0%,#8a6a4e 40%,#5b3a2a 70%,#a8584a 100%)}
.arrow{position:absolute;top:185px;color:#fff;font-size:22px}
h2{font-weight:700;text-transform:uppercase;text-align:center}
.welcome-title{top:690px;left:0;width:1200px;font-size:26px;color:var(--green)}
.lede{top:728px;left:134px;width:932px;font-size:11.5px;line-height:1.9;text-align:center;color:#555}
.sub{text-transform:uppercase;font-size:13px;color:var(--magenta);text-align:center;width:1200px;left:0}
.gallery{top:880px;left:134px;width:932px;display:flex;justify-content:space-between}
.gallery div{width:224px;height:160px}
.dots{top:1062px;left:0;width:1200px;display:flex;justify-content:center;gap:14px}
.dots span{width:10px;height:10px;border:1px solid #bbb;border-radius:50%}
.dots span.on{background:#bbb}
.day{top:1159px;left:0;width:1200px;height:358px;background:var(--magenta)}
.day .photo{position:absolute;left:134px;top:60px;width:439px;height:172px;background:linear-gradient(135deg,#a7d7d4,#e8ddd0 60%,#b79a86)}
.day h3{position:absolute;left:625px;top:52px;color:#fff;font-size:23px;font-weight:700;text-transform:uppercase}
.day p{position:absolute;left:625px;top:95px;width:445px;color:#fff;font-size:11px;line-height:1.85}
.btn{display:inline-block;border:1px solid #fff;color:#fff;font-size:12px;padding:11px 16px;text-decoration:none}
.day .btn{position:absolute;left:625px;top:262px}
.staff-title{top:1590px;left:0;width:1200px;font-size:24px;color:var(--green)}
.staff{top:1639px;left:134px;width:932px;display:flex;justify-content:space-between}
.member{width:178px;text-align:center}
.member .pic{height:178px;background:linear-gradient(180deg,#cfc9c2,#9c8e82)}
.member .name{color:var(--green);font-size:16px;margin-top:14px}
.member .role{color:var(--muted);font-size:9px;margin-top:4px}
.accreds{top:1950px;left:134px;width:932px;display:flex;justify-content:space-between;align-items:center}
.accreds span{font-weight:800;font-size:17px;color:#222;letter-spacing:.5px}
.pricing{top:2061px;left:0;width:1200px;height:829px;background:var(--navy)}
.pricing h2{color:#fff;font-size:24px;margin-top:78px}
table{position:absolute;left:134px;top:122px;width:932px;border-collapse:collapse}
th{background:var(--green-bright);color:#fff;font-size:24px;height:49px;border-right:2px solid var(--navy)}
td{background:var(--row);height:97px;border-top:5px solid var(--navy);border-right:2px solid var(--navy);text-align:center;font-size:24px;font-weight:700;color:#222}
td.label{text-align:left;padding-left:28px;width:312px}
td.label b{display:block;font-size:25px;text-transform:uppercase;line-height:1.05}
td small{display:block;font-size:12px;font-weight:400}
th:last-child,td:last-child{border-right:none}
.notes{position:absolute;top:630px;left:0;width:1200px;text-align:center;color:#fff;font-size:12px;line-height:2}
.pricing .btn{position:absolute;left:552px;top:720px}
.fb-title{top:2960px;left:134px;font-size:22px;color:var(--green);font-weight:700;text-transform:uppercase}
.like{top:2968px;left:1020px;width:46px;height:20px;border:1px solid #aaa;border-radius:3px;font-size:10px;text-align:center;line-height:18px;color:#3b5998}
.post{top:3012px;width:456px;height:159px;border:1px solid #ccc;padding:18px 20px}
.post .av{position:absolute;left:20px;top:18px;width:38px;height:38px;background:#dde}
.post .who{margin-left:50px;font-size:12px;color:var(--navy)}
.post .who span{color:#555}
.post .when{margin-left:50px;font-size:9px;color:#888;margin-top:2px}
.post p{margin-left:50px;margin-top:12px;font-size:9.5px;color:#777;line-height:1.7}
.info{top:3251px;left:0;width:1200px;height:120px;background:var(--light)}
.info .col{position:absolute;top:30px;font-size:11px;color:#444;line-height:1.7}
.info .col b{display:flex;align-items:center;gap:6px;font-size:14px;font-weight:600;color:#333;margin-bottom:4px}
.footer{top:3371px;left:0;width:1200px;height:288px;background:var(--footer);color:#ccc}
.flinks{position:absolute;left:134px;top:30px;font-size:11px}
.flinks a{color:#ddd;text-decoration:none}
.copy{position:absolute;left:134px;top:54px;font-size:11px;color:#ddd}
.social{position:absolute;left:134px;top:96px;display:flex;gap:16px}
.social span{width:14px;height:14px;background:#888}
.badges{position:absolute;left:606px;top:32px;display:flex;gap:14px}
.badge{width:100px;height:82px;background:#fff;color:var(--navy);font-weight:800;font-size:11px;text-align:center;padding-top:20px;line-height:1.2}
.seal{width:94px;height:82px;background:var(--navy);border-radius:8px}
.rule{position:absolute;left:134px;top:142px;width:932px;height:1px;background:#555}
.legal{position:absolute;left:134px;top:168px;width:932px;font-size:8.5px;line-height:1.7;color:#aaa}
</style>
</head>
<body>
<header class="header">
  <div class="brand" style="left:110px"><span class="dot"></span>BRIGHT BEARS<br>QRP</div>
  <div class="brand" style="left:880px"><span class="dot"></span>BRIGHT BEARS<br>KWS</div>
</header>
<nav class="nav">
  <a class="active" href="#">HOME</a><a href="#">ABOUT US</a><a href="#">SERVICES</a><a href="#">PRICING</a><a href="#">PHOTO GALLERY</a><a href="#">CONTACT US</a>
</nav>
<div class="hero" role="img" aria-label="Nursery playroom with toys, shelves and a decorated tree"></div>
<span class="arrow" style="top:400px;left:4px">&#8249;</span><span class="arrow" style="top:400px;left:1186px">&#8250;</span>

<h2 class="abs welcome-title">Welcome to Bright Bears Day Nursery QRP</h2>
<p class="abs lede">Pellentesque a imperdiet dolor, et auctor est. Fusce sollicitudin lorem et luctus volutpat. Proin placerat dapibus gravida. In tristique tristique nulla eget hendrerit. Maecenas vel tortor accumsan quam varius imperdiet vel eget elit. Aenean facilisis tincidunt lectus, id dictum nisi luctus eget. Vivamus efficitur ex condimentum, malesuada eros eget, feugiat nibh. Sed tellus ex, imperdiet eget gravida sit amet, volutpat eget turpis. In nec ultricies est. Etiam mattis augue vehicula odio posuere, sit amet tempus lectus luctus. Nulla facilisi. Etiam vel massa elementum, bibendum tellus venenatis, feugiat massa. Curabitur venenatis lacinia ornare. Cras sollicitudin cursus.</p>
<p class="abs sub" style="top:842px">Our Nursery</p>
<div class="abs gallery">
  <div role="img" aria-label="Play kitchen corner" style="background:linear-gradient(135deg,#7a4a3a,#c79a6a)"></div>
  <div role="img" aria-label="Craft table with festive paper" style="background:linear-gradient(135deg,#3b2a24,#a8343a)"></div>
  <div role="img" aria-label="Decorated activity table" style="background:linear-gradient(135deg,#5a3a30,#b24a40)"></div>
  <div role="img" aria-label="Quiet reading area" style="background:linear-gradient(135deg,#4a6d8e,#9aa8b8)"></div>
</div>
<div class="abs dots"><span class="on"></span><span></span><span></span><span></span></div>

<section class="abs day">
  <div class="photo" role="img" aria-label="Baby room with cushions and soft toys"></div>
  <h3>Description of our day</h3>
  <p>Aliquam erat volutpat. Quisque aliquet ex nec est vestibulum pulvinar. Pellentesque convallis molestie enim sit amet efficitur. Etiam id imperdiet lectus. Vivamus lacus justo, ultrices nec erat in, euismod iaculis mauris. Vivamus eleifend vitae nulla vel malesuada. In at malesuada lacus, et consectetur ante. Fusce vitae lectus sit amet mi pulvinar maximus. Aenean placerat, nibh vel accumsan aliquet, magna nibh accumsan nibh, ac tempus nunc ipsum ac tellus. Cras augue magna, placerat eget nulla non, congue suscipit neque. Praesent iaculis faucibus urna sit amet lacinia.</p>
  <a class="btn" href="#">Read more</a>
</section>

<h2 class="abs staff-title">Our Staffs</h2>
<div class="abs staff">
  <div class="member"><div class="pic" role="img" aria-label="Staff member portrait"></div><div class="name">Sam Rowe</div><div class="role">Phasellus nisl est, condimentum</div></div>
  <div class="member"><div class="pic" role="img" aria-label="Staff member portrait"></div><div class="name">Sam Rowe</div><div class="role">Phasellus nisl est, condimentum</div></div>
  <div class="member"><div class="pic" role="img" aria-label="Staff member portrait"></div><div class="name">Sam Rowe</div><div class="role">Phasellus nisl est, condimentum</div></div>
  <div class="member"><div class="pic" role="img" aria-label="Staff member portrait"></div><div class="name">Sam Rowe</div><div class="role">Phasellus nisl est, condimentum</div></div>
  <div class="member"><div class="pic" role="img" aria-label="Staff member portrait"></div><div class="name">Sam Rowe</div><div class="role">Phasellus nisl est, condimentum</div></div>
</div>
<p class="abs sub" style="top:1902px">Training Accreditations</p>
<div class="abs accreds"><span>LUMO</span><span>TIDEWELL</span><span>BRISK</span><span>HARBOUR</span><span>MARLO</span><span>PIPPA</span><span>KITEBAY</span></div>

<section class="abs pricing">
  <h2>Pricing</h2>
  <table>
    <tr><th></th><th>UNDER 2'S</th><th>2-5'S</th></tr>
    <tr><td class="label"><b>Half Day</b><small>8am-1pm or 1pm-6pm</small></td><td>£26</td><td>£25</td></tr>
    <tr><td class="label"><b>Full Day</b><small>(7.30-6pm)</small></td><td>£40</td><td>£38</td></tr>
    <tr><td class="label"><b>Full Time</b><small>Mon- Fri 7.30-6pm</small></td><td>£168</td><td>£161<small>(Funded children in holidays)</small></td></tr>
    <tr><td class="label"><b>Full Time Funded Children</b><small>3+ years old*</small></td><td>XXX</td><td>£130<small>During term time</small></td></tr>
  </table>
  <p class="notes">Fees include breakfast (full day/full time only). A light snack each session, nappies and wipes.<br>Meals can be offered for an additional charge (£2.50 per meal, per day).<br>Please see a member of staff!</p>
  <a class="btn" href="#">Read more</a>
</section>

<h2 class="abs fb-title">Chatterbook Feeds</h2>
<div class="abs like">Like</div>
<article class="abs post" style="left:134px"><div class="av"></div><div class="who">Bright Bears Day Nursery QRP <span>@brightbearsqrp</span></div><div class="when">July 6 at 3:23pm</div><p>CALLING ALL PARENTS/CARERS WITH 2,3 &amp; 4 YEAR OLDS! DON'T FORGET TIME IS RUNNING OUT TO APPLY FOR FUNDING/SUPPORT WITH CHILDCARE FEES FROM SEPT '17! VISIT THE L...</p></article>
<article class="abs post" style="left:610px"><div class="av"></div><div class="who">Bright Bears Day Nursery QRP <span>@brightbearsqrp</span></div><div class="when">July 6 at 3:23pm</div><p>CALLING ALL PARENTS/CARERS WITH 2,3 &amp; 4 YEAR OLDS! DON'T FORGET TIME IS RUNNING OUT TO APPLY FOR FUNDING/SUPPORT WITH CHILDCARE FEES FROM SEPT '17! VISIT THE L...</p></article>

<section class="abs info">
  <div class="col" style="left:134px"><b><svg width="13" height="13" viewBox="0 0 14 14"><circle cx="7" cy="7" r="6" fill="none" stroke="#333" stroke-width="1.6"/><path d="M7 3.5V7l2.5 1.5" stroke="#333" stroke-width="1.4" fill="none"/></svg>Opening Hours</b>Mon - Fri : 10 Am - 4 PM<br>Sat - Sun : Holiday</div>
  <div class="col" style="left:382px"><b><svg width="11" height="14" viewBox="0 0 11 14"><path d="M5.5 0C2.5 0 0 2.4 0 5.4 0 9 5.5 14 5.5 14S11 9 11 5.4C11 2.4 8.5 0 5.5 0z" fill="#333"/><circle cx="5.5" cy="5.3" r="2" fill="#f0f0f0"/></svg>Address</b>Harbourside leisure centre<br>Seaton SE4 1AB</div>
  <div class="col" style="left:660px"><b><svg width="10" height="14" viewBox="0 0 10 14"><rect x="0.5" y="0.5" width="9" height="13" rx="1.5" fill="#333"/><rect x="2" y="2" width="6" height="8.5" fill="#f0f0f0"/></svg>Phone</b>+44 7700 900142</div>
  <div class="col" style="left:906px"><b><svg width="14" height="11" viewBox="0 0 14 11"><rect width="14" height="11" rx="1" fill="#333"/><path d="M1 1.5l6 4.5 6-4.5" stroke="#f0f0f0" stroke-width="1.3" fill="none"/></svg>Email</b>info@brightbearsnursery.example</div>
</section>

<footer class="abs footer">
  <div class="flinks"><a href="#">Home</a> &nbsp;|&nbsp; <a href="#">About Us</a> &nbsp;|&nbsp; <a href="#">Services</a> &nbsp;|&nbsp; <a href="#">Pricing</a> &nbsp;|&nbsp; <a href="#">Photo Gallery</a> &nbsp;|&nbsp; <a href="#">Contact Us</a></div>
  <div class="copy">Copyright © 2017 Bright Bears Day Nursery QRP. All rights reserved.</div>
  <div class="social"><span></span><span></span></div>
  <div class="badges">
    <div class="badge">BRIGHT BEARS<br>QRP</div>
    <div class="badge">BRIGHT BEARS<br>KWS</div>
    <div class="seal"></div>
    <div class="seal"></div>
  </div>
  <div class="rule"></div>
  <p class="legal">Privacy Policy - Maecenas vel tortor accumsan quam varius imperdiet vel eget elit. Aenean facilisis tincidunt lectus, id dictum nisi luctus eget. Vivamus efficitur ex condimentum, malesuada eros eget, feugiat nibh. Sed tellus ex, imperdiet eget gravida sit amet, volutpat eget turpis. In nec ultricies est. Etiam mattis augue vehicula odio posuere, sit amet tempus lectus luctus. Nulla facilisi. Etiam vel massa elementum, bibendum tellus venenatis, feugiat massa. Aliquam erat volutpat. Quisque aliquet ex nec est vestibulum pulvinar. Pellentesque convallis molestie enim sit amet efficitur. Etiam id imperdiet lectus. Vivamus lacus justo, ultrices nec erat in, euismod iaculis mauris. Vivamus eleifend vitae nulla vel malesuada. In at malesuada lacus.</p>
</footer>
</body>
</html>
```